Healthcare and Professional IT Services Company need a redesigned business card

We are a IT Services company that targets small medical practices and professional business such as Attorneys, Accounts, Architects etc. We want to communicate a professional yet friendly image using recent logo redesign here on ArtHarbor. Like to see the colors blue and orange in the design. Must use the Tall Pine Computing as displayed in the new logo - then also want to incorporate the fish logo as well.

Target Market(s)

Small medical and professional services

Industry/Entity Type

It Company

Contact Information for Business Card

The usual stuff, place for name address phone website. Also maybe our tagline which is "Rooted in reliable tech"

Requirements
Must have
• My new logo and the fish somewhere on the card

```html
<!DOCTYPE html>
<html lang="en">
<head>
<meta charset="utf-8">
<title>Tall Pine Computing – Business Card</title>
<link rel="stylesheet" href="https://fonts.googleapis.com/css2?family=Quicksand:wght@400;500;600&family=Open+Sans:wght@400&display=swap">
<style>
  :root {
    --backdrop: #3a3a3a;
    --paper: #f7f7f7;
    --brand-blue: #1f9ad9;
    --card-blue: #0a92d6;
    --mascot-light: #5bb8e6;
    --mascot-mid: rgba(44, 162, 221, 0.6);
    --ink: #4a4a4a;
    --white: #ffffff;
  }
  * { box-sizing: border-box; margin: 0; padding: 0; }
  html, body {
    width: 1200px; height: 750px; overflow: hidden;
    background: var(--backdrop);
  }
  .stage { position: relative; width: 1200px; height: 750px; }
  .card {
    position: absolute; top: 228px; width: 462px; height: 262px;
    overflow: hidden;
  }
  .card--front { left: 124px; background: var(--paper); font-family: "Quicksand", sans-serif; }
  .card--back { left: 618px; background: var(--card-blue); }

  /* front */
  .front__mascot {
    position: absolute; left: 40px; top: 26px; width: 120px; height: 86px;
    border-radius: 40px;
    background: radial-gradient(ellipse at center, #d3ebf8 0%, #eaf5fb 60%, var(--paper) 100%);
  }
  .front__wordmark {
    position: absolute; left: 23px; top: 120px; white-space: nowrap;
    font-weight: 600; font-size: 27px; line-height: 1; color: var(--brand-blue);
  }
  .name-band {
    position: absolute; right: 0; top: 26px; width: 166px; height: 58px;
    background: var(--brand-blue); color: var(--white); text-align: right;
    padding: 9px 28px 0 0;
  }
  .name-band__name { font-size: 21px; font-weight: 400; line-height: 1.1; }
  .name-band__role { font-size: 13px; font-weight: 400; line-height: 1.2; }
  .contact {
    position: absolute; left: 23px; top: 188px; list-style: none;
    font-size: 12.5px; color: var(--ink);
  }
  .contact li { display: flex; align-items: center; height: 19px; }
  .contact svg { width: 11px; height: 11px; margin-right: 7px; fill: var(--brand-blue); }
  .address {
    position: absolute; right: 28px; top: 209px; text-align: right;
    font-size: 12.5px; color: var(--ink); line-height: 16px; font-style: normal;
  }

  /* back */
  .back__mascot {
    position: absolute; left: 0; top: 0; width: 262px; height: 262px;
    background: radial-gradient(ellipse at 55% 50%, var(--mascot-light) 0%, var(--mascot-mid) 45%, rgba(10, 146, 214, 0) 72%);
  }
  .back__brand {
    position: absolute; left: 268px; width: 180px; top: 160px; text-align: center; color: var(--white);
  }
  .back__wordmark {
    font-family: "Quicksand", sans-serif; font-weight: 600; font-size: 24px; line-height: 1.05;
  }
  .back__tagline {
    font-family: "Open Sans", sans-serif; font-size: 12.5px; margin-top: 7px; white-space: nowrap;
  }
</style>
</head>
<body>
<main class="stage">
  <section class="card card--front">
    <div class="front__mascot" role="img" aria-label="Cartoon fish mascot illustration"></div>
    <div class="front__wordmark">Tall Pine Computing</div>
    <div class="name-band">
      <p class="name-band__name">Owen Hale</p>
      <p class="name-band__role">CEO/Founder</p>
    </div>
    <ul class="contact">
      <li><svg viewBox="0 0 24 24" aria-hidden="true"><path d="M6.6 10.8a15.1 15.1 0 0 0 6.6 6.6l2.2-2.2a1 1 0 0 1 1-.25 11.4 11.4 0 0 0 3.6.57 1 1 0 0 1 1 1V20a1 1 0 0 1-1 1A17 17 0 0 1 3 4a1 1 0 0 1 1-1h3.5a1 1 0 0 1 1 1c0 1.25.2 2.45.57 3.57a1 1 0 0 1-.25 1z"/></svg>555 014 7781</li>
      <li><svg viewBox="0 0 24 24" aria-hidden="true"><path d="M2 5h20v14H2z M2 5l10 8 10-8" /></svg>hello@tallpinepc.com</li>
      <li><svg viewBox="0 0 24 24" aria-hidden="true"><circle cx="12" cy="12" r="11"/></svg>www.tallpinepc.com</li>
    </ul>
    <address class="address">2143 Cedar Hollow Road<br>Juneau, Alaska 99801</address>
  </section>

  <section class="card card--back">
    <div class="back__mascot" role="img" aria-label="Large cartoon fish mascot illustration in white outline"></div>
    <div class="back__brand">
      <p class="back__wordmark">Tall Pine<br>Computing</p>
      <p class="back__tagline">Rooted in reliable tech</p>
    </div>
  </section>
</main>
</body>
</html>
```